KAJU Freightways #ALLKAJU Business Cards & Letterhead

I am looking to business cards designed for our organization. We are currently undergoing a small re-branding that is taking place. Our organization is called KAJU Freightways and we are headquartered in Phoenix, AZ. We primarily provide transportation and logistics services to the Marlow Parcel Bureau who is our largest customer. I would like to see a design that incorporates name, title, contact info, website, and address (this will be different depending on the employee). I would also like to see some color on the business card using our logo colors or a variation. I would like our logo on the back of the business card with the website displayed. The final design should communicate that we are a next generation transportation operate that focuses on being driver-first, customer-centric, innovative, and sustainable.We would also like our #ALLKAJU catch phrase incorporated as well.

Target Market(s)

Transportation & Logistics

Industry/Entity Type

Trucking Company

Contact Information for Business Card

-First and Last Name
-Position Title
-Contact Phone
-Contact Email
-Physical Address

Font styles to use
Serif

Colors

Designer to choose colors to be used in the design.

Requirements
Must have
• -KAJU logo prominently displayed
• -#ALLKAJU catch phrase used
• -Some amount of color, design gradient, etc.
• -Logo on the back with website listed (https://www.kajufreightco.example)

```html
<!DOCTYPE html>
<html lang="en">
<head>
<meta charset="utf-8">
<title>KAJU Freightways Business Card</title>
<link href="https://fonts.googleapis.com/css2?family=Source+Serif+4:opsz,wght@8..60,400;8..60,600;8..60,700&display=swap" rel="stylesheet">
<style>
  :root {
    --page-bg: #3a3431;
    --card-bg: #0d0d0d;
    --ink: #ffffff;
    --ink-soft: #d9d9d9;
    --accent: #f29a2e;
    --accent-deep: #d9482b;
    --accent-gradient: linear-gradient(90deg, var(--accent), var(--accent-deep));
    --rule: #4a4a4a;
  }
  * { box-sizing: border-box; margin: 0; padding: 0; }
  html, body { width: 1200px; height: 844px; overflow: hidden; }
  body {
    background: var(--page-bg);
    font-family: "Source Serif 4", Georgia, serif;
    color: var(--ink);
    position: relative;
  }
  .card {
    position: absolute;
    top: 272px;
    width: 520px;
    height: 300px;
    background: var(--card-bg);
    box-shadow: 0 12px 30px rgba(0,0,0,.45);
    overflow: hidden;
  }
  .card--front { left: 50px; }
  .card--back { left: 630px; }
  .card-band {
    position: absolute; left: 0; right: 0; bottom: 0; height: 6px;
    background: var(--accent-gradient);
  }

  .brand-name {
    font-weight: 700; font-size: 48px; letter-spacing: 1px; color: var(--ink);
    line-height: 1;
  }
  .brand-dot {
    width: 18px; height: 18px; border-radius: 50%; background: var(--accent);
    flex: none;
  }

  /* front */
  .front-brand {
    position: absolute; left: 0; top: 0; width: 260px; height: 300px;
    display: flex; align-items: center; justify-content: center; gap: 12px;
  }
  .front-divider {
    position: absolute; left: 268px; top: 40px; width: 2px; height: 214px;
    background: linear-gradient(180deg, var(--accent), var(--accent-deep));
  }
  .contact {
    position: absolute; left: 288px; top: 58px; right: 14px;
    font-size: 13px; line-height: 1.35; color: var(--ink-soft);
  }
  .contact-name { font-weight: 700; font-size: 19px; color: var(--ink); letter-spacing: .5px; line-height: 1.2; }
  .contact-title { font-size: 13px; margin-bottom: 6px; color: var(--accent); }
  .contact-line { display: flex; align-items: center; gap: 7px; font-size: 13px; white-space: nowrap; }
  .contact-line svg { width: 12px; height: 12px; flex: none; fill: var(--accent); }
  .contact-address { margin-top: 8px; font-size: 13px; }

  /* back */
  .back-brand {
    position: absolute; left: 0; right: 0; top: 62px;
    display: flex; align-items: center; justify-content: center; gap: 12px;
  }
  .back-brand .brand-name { font-size: 52px; }
  .back-rule {
    position: absolute; left: 30px; right: 30px; top: 176px; height: 2px;
    background: var(--accent-gradient);
  }
  .tagline {
    position: absolute; right: 30px; top: 150px; font-size: 14px; font-weight: 600;
    letter-spacing: .5px; color: var(--accent);
  }
  .website {
    position: absolute; left: 30px; bottom: 36px; font-size: 14px; color: var(--ink-soft);
  }
</style>
</head>
<body>
  <section class="card card--front" aria-label="Business card front">
    <div class="front-brand">
      <span class="brand-dot"></span>
      <span class="brand-name">KAJU</span>
    </div>
    <div class="front-divider"></div>
    <div class="contact">
      <p class="contact-name">MARCUS HALE</p>
      <p class="contact-title">Managing Director</p>
      <p class="contact-line">
        <svg viewBox="0 0 24 24" aria-hidden="true"><path d="M6.6 10.8a15.1 15.1 0 0 0 6.6 6.6l2.2-2.2a1 1 0 0 1 1-.25 11.4 11.4 0 0 0 3.6.57 1 1 0 0 1 1 1V20a1 1 0 0 1-1 1A17 17 0 0 1 3 4a1 1 0 0 1 1-1h3.5a1 1 0 0 1 1 1c0 1.25.2 2.45.57 3.57a1 1 0 0 1-.25 1z"/></svg>
        044-987 654 321
      </p>
      <p class="contact-line">
        <svg viewBox="0 0 24 24" aria-hidden="true"><path d="M2 5h20v14H2zm2 2v.5l8 5 8-5V7z"/></svg>
        hello@kajufreightco.example
      </p>
      <p class="contact-line">
        <svg viewBox="0 0 24 24" aria-hidden="true"><circle cx="12" cy="12" r="10"/></svg>
        www.kajufreightco.example
      </p>
      <p class="contact-address">KAJU Freightways<br>88, Copper Ridge Road<br>85004, Phoenix AZ</p>
    </div>
    <div class="card-band"></div>
  </section>

  <section class="card card--back" aria-label="Business card back">
    <div class="back-brand">
      <span class="brand-dot"></span>
      <span class="brand-name">KAJU</span>
    </div>
    <p class="tagline">#ALLKAJU</p>
    <div class="back-rule"></div>
    <p class="website">www.kajufreightco.example</p>
    <div class="card-band"></div>
  </section>
</body>
</html>
```